Design a single page Shopify store web page

We are looking to have a page designed for a single page Shopify store with 2 products. We already have a basic structure that we like, though we are open to suggestions. We are looking for somebody to provide a design/color scheme that we can then implement using Shopify's templating system. We can handle the implementation(HTML / CSS / jS) as we already have 2 web developers on the team, but have not been able to find a design we liked.

The job would consist of providing a mockup (photoshop or otherwise) and any vector graphics you choose to create for the site (we can provide product photos and other images).

You can also look at http://brickdune.com.au for some of our design direction we have used so far

Target Market(s)

Young Australian Males (18 - 49)

Industry/Entity Type

Store

Number of Pages Required

1 page

Font styles to use
Serif
Sans Serif

Requirements
Must have
• Single Page Design
• E-commerce Product Purchase
• Manly (whatever interpretation of that you have)

```html
<!DOCTYPE html>
<html lang="en">
<head>
<meta charset="utf-8">
<title>Stock Up – Underwear &amp; Socks Delivered</title>
<link href="https://fonts.googleapis.com/css2?family=Open+Sans:wght@400;600;700;800&display=swap" rel="stylesheet">
<style>
:root{
  --navy:#11283a;
  --green:#3fbe94;
  --green-card:#35ac85;
  --green-bar:#33a57f;
  --green-text:#2fb487;
  --grey-text:#7a7f84;
  --logo:#9aa9b4;
}
*{margin:0;padding:0;box-sizing:border-box}
html,body{width:1200px;height:2353px;overflow:hidden;background:#fff}
body{position:relative;font-family:"Open Sans",Arial,sans-serif;color:var(--navy)}
.abs{position:absolute}

/* header */
.site-header{left:0;top:0;width:1200px;height:100px;background:var(--navy);border-bottom:2px solid #2f4a5c}
.brand{left:133px;top:28px;height:44px;display:flex;align-items:center;gap:12px;color:var(--logo);font-weight:700;font-size:34px;letter-spacing:1px}
.brand-dot{width:40px;height:40px;border-radius:50%;background:var(--logo)}
.main-nav a{position:absolute;top:38px;color:#fff;font-size:14px;font-weight:400;text-decoration:none;letter-spacing:.3px}
.signup{left:951px;top:28px;width:116px;height:36px;border:1.5px solid #fff;color:#fff;font-size:12px;display:flex;align-items:center;justify-content:center;letter-spacing:.3px}

/* hero */
.hero{left:0;top:100px;width:1200px;height:521px;background:var(--navy)}
.hero svg.bg{position:absolute;left:0;top:0}
.hero-title{left:570px;top:80px;width:630px;text-align:center;color:#fff;font-weight:700;font-size:52px;letter-spacing:1px}
.hero-line{left:620px;width:570px;text-align:center;font-weight:700;font-size:34px;color:var(--navy);letter-spacing:.5px}
.hero-line .w{color:#fff}
.slide-btn{top:479px;width:34px;height:30px;border:1.5px solid #fff}
.slide-btn svg{position:absolute;left:11px;top:7px}

/* how it works */
.section-title{left:0;width:1200px;text-align:center;font-weight:700;font-size:52px;color:var(--navy)}
.intro{left:180px;top:726px;width:840px;text-align:center;font-family:Arial,sans-serif;font-size:11px;line-height:23px;color:var(--grey-text)}
.step{width:320px;text-align:center}
.step-ring{display:block;margin:0 auto}
.step-name{margin-top:26px;font-size:18px;font-weight:600;color:var(--green-text)}
.step-text{margin-top:6px;font-family:Arial,sans-serif;font-size:11px;line-height:17px;color:var(--grey-text)}

/* plans */
.plans{left:0;top:1106px;width:1200px;height:545px;background:linear-gradient(135deg,#46c69b,#3bb88e 55%,#42c197)}
.plans .section-title{color:#fff;top:22px}
.plan-card{top:113px;width:444px;height:331px;background:var(--green-card)}
.plan-name{left:9px;top:22px;color:#fff;font-weight:700;font-size:16px}
.plan-photo{left:11px;top:56px;width:263px;height:264px}
.plan-option{left:301px;width:129px;height:44px;background:#fff;color:var(--green-text);font-size:11px;font-weight:700;display:flex;align-items:center;justify-content:center}
.plan-price{left:301px;top:182px;width:129px;text-align:center;color:#fff;font-weight:700;font-size:54px}
.plan-buy{left:301px;top:264px;width:129px;height:56px;background:var(--navy);color:#fff;font-weight:700;font-size:29px;display:flex;align-items:center;justify-content:center}
.perks{left:132px;top:468px;width:935px;height:50px;background:var(--green-bar);display:flex;align-items:center;justify-content:space-around;color:#fff;font-weight:700;font-size:14px}
.perk{display:flex;align-items:center;gap:12px}

/* faq */
.faq-item{width:292px}
.faq-head{display:flex;align-items:flex-start;gap:10px;height:40px}
.faq-head h3{max-width:245px;font-size:16px;font-weight:700;line-height:19px;color:var(--navy);padding-top:3px}
.faq-item p{margin-top:2px;font-family:Arial,sans-serif;font-size:10.5px;line-height:21px;color:var(--grey-text)}

/* footer */
.site-footer{left:0;top:2229px;width:1200px;height:124px;background:var(--navy);color:#fff}
.foot-links{left:132px;top:32px;font-size:11px}
.copyright{left:132px;top:73px;font-size:11px}
.social{top:17px;width:36px;height:36px;border:2px solid #fff;border-radius:50%}
.pay{top:76px;width:36px;height:22px;border-radius:2px}
</style>
</head>
<body>

<header class="abs site-header">
  <div class="abs brand"><span class="brand-dot"></span>STOCK UP</div>
  <nav class="main-nav">
    <a style="left:490px">HOW IT WORKS</a>
    <a style="left:653px">PLANS</a>
    <a style="left:756px">FAQ</a>
    <a style="left:846px">ABOUT US</a>
  </nav>
  <div class="abs signup">SIGN UP NOW</div>
</header>

<section class="abs hero">
  <svg class="bg" width="1200" height="521">
    <defs>
      <linearGradient id="model" x1="0" y1="0" x2="1" y2="1">
        <stop offset="0" stop-color="#b6754f"/>
        <stop offset=".6" stop-color="#8a5236"/>
        <stop offset="1" stop-color="#2a1d18"/>
      </linearGradient>
    </defs>
    <rect x="95" y="0" width="330" height="521" fill="url(#model)" role="img" aria-label="Photo of a muscular man wearing dark briefs"/>
    <polygon points="463,0 1200,0 1200,521 769,521" fill="var(--green)"/>
    <line x1="463" y1="0" x2="769" y2="521" stroke="#6fd9b4" stroke-width="3"/>
  </svg>
  <div class="abs hero-title">AUTOMATE YOUR LIFE</div>
  <div class="abs hero-line" style="top:176px">NEW <span class="w">UNDERWEAR</span> AND <span class="w">SOCKS</span></div>
  <div class="abs hero-line" style="top:237px">DELIVERED TO YOU DOOR</div>
  <div class="abs hero-line" style="top:298px"><span class="w">WHENYOUU NEED IT</span></div>
  <div class="abs slide-btn" style="left:993px"><svg width="10" height="14" viewBox="0 0 10 14"><path d="M8 1 2 7l6 6" fill="none" stroke="#fff" stroke-width="2"/></svg></div>
  <div class="abs slide-btn" style="left:1035px"><svg width="10" height="14" viewBox="0 0 10 14"><path d="M2 1l6 6-6 6" fill="none" stroke="#fff" stroke-width="2"/></svg></div>
</section>

<h2 class="abs section-title" style="top:646px">HOW IT WORKS</h2>
<p class="abs intro">Sed ut perspiciatis unde omnis iste natus error sit voluptatem accusantium doloremque laudantium, totam rem aperiam, eaque ipsa quae ab illo inventore veritatis<br>et quasi architecto beatae vitae dicta sunt explicabo.</p>

<div class="abs step" style="left:122px;top:796px">
  <svg class="step-ring" width="190" height="190" viewBox="0 0 190 190">
    <circle cx="95" cy="95" r="90" fill="none" stroke="var(--navy)" stroke-width="6"/>
    <path d="M95 5a90 90 0 0 1 90 90" fill="none" stroke="var(--green)" stroke-width="6"/>
    <circle cx="95" cy="92" r="42" fill="var(--green)"/>
    <text x="95" y="112" text-anchor="middle" font-family="Open Sans,sans-serif" font-weight="800" font-size="54" fill="#fff">?</text>
  </svg>
  <div class="step-name">CHOOSE A PLAN</div>
  <div class="step-text">There will be plans for all budgets and styles.</div>
</div>

<div class="abs step" style="left:438px;top:796px">
  <svg class="step-ring" width="190" height="190" viewBox="0 0 190 190">
    <circle cx="95" cy="95" r="90" fill="none" stroke="var(--navy)" stroke-width="6"/>
    <path d="M95 185a90 90 0 0 1-90-90" fill="none" stroke="var(--green)" stroke-width="6"/>
    <g fill="none" stroke="var(--green)" stroke-width="5">
      <rect x="55" y="55" width="26" height="26"/><rect x="55" y="103" width="26" height="26"/>
      <path d="M60 67l7 7 16-18M60 115l7 7 16-18"/>
    </g>
    <g fill="var(--green)"><rect x="92" y="60" width="46" height="7"/><rect x="92" y="72" width="32" height="7"/><rect x="92" y="108" width="46" height="7"/><rect x="92" y="120" width="32" height="7"/></g>
  </svg>
  <div class="step-name">CHOOSE HOW OFTEN</div>
  <div class="step-text">Decide whether you would like to receive<br>new packages every 3 or 6 months.</div>
</div>

<div class="abs step" style="left:761px;top:796px">
  <svg class="step-ring" width="190" height="190" viewBox="0 0 190 190">
    <circle cx="95" cy="95" r="90" fill="none" stroke="var(--navy)" stroke-width="6"/>
    <path d="M5 95a90 90 0 0 1 90-90" fill="none" stroke="var(--green)" stroke-width="6"/>
    <polygon points="55,80 95,92 135,80 135,125 95,140 55,125" fill="var(--green)"/>
    <polygon points="55,80 40,62 80,52 95,70 110,52 150,62 135,80 95,70" fill="var(--green)" stroke="#fff" stroke-width="3"/>
    <line x1="95" y1="92" x2="95" y2="140" stroke="#fff" stroke-width="3"/>
  </svg>
  <div class="step-name">GET YOUR PACK</div>
  <div class="step-text">We'll send out your first pack right away and<br>then again every 3 or 6 months.</div>
</div>

<section class="abs plans">
  <h2 class="abs section-title">PLANS</h2>

  <article class="abs plan-card" style="left:132px">
    <div class="abs plan-name">COMFORT</div>
    <div class="abs plan-photo" role="img" aria-label="Product photo of a man wearing dark trunks" style="background:linear-gradient(160deg,#2b3a2a,#b8763f 50%,#1d2430)"></div>
    <div class="abs plan-option" style="top:57px">CUSTOMISING PLANS</div>
    <div class="abs plan-option" style="top:110px">CUSTOMISING PLANS</div>
    <div class="abs plan-price">$ 30</div>
    <div class="abs plan-buy">GET IT!</div>
  </article>

  <article class="abs plan-card" style="left:623px">
    <div class="abs plan-name">STYLE</div>
    <div class="abs plan-photo" role="img" aria-label="Product photo of a man wearing black briefs" style="background:linear-gradient(160deg,#c9ccd3,#9a6446 50%,#2a2220)"></div>
    <div class="abs plan-option" style="top:57px">CUSTOMISING PLANS</div>
    <div class="abs plan-option" style="top:110px">CUSTOMISING PLANS</div>
    <div class="abs plan-price">$ 30</div>
    <div class="abs plan-buy">GET IT!</div>
  </article>

  <div class="abs perks">
    <div class="perk"><svg width="34" height="28" viewBox="0 0 34 28" fill="none" stroke="#fff" stroke-width="2.5"><path d="M1 2h6l4 16h18l4-12H9"/><circle cx="13" cy="24" r="2.5"/><circle cx="27" cy="24" r="2.5"/></svg>FREE SHIPPING</div>
    <div class="perk"><svg width="34" height="30" viewBox="0 0 34 30" fill="#fff"><rect x="2" y="20" width="5" height="10"/><rect x="10" y="15" width="5" height="15"/><rect x="18" y="10" width="5" height="20"/><rect x="26" y="4" width="5" height="26"/></svg>EASY RETURNS</div>
    <div class="perk"><svg width="24" height="24" viewBox="0 0 24 24" stroke="#fff" stroke-width="4"><path d="M3 3l18 18M21 3 3 21"/></svg>CANCEL WHENEVER</div>
    <div class="perk"><svg width="30" height="30" viewBox="0 0 30 30" fill="none" stroke="#fff" stroke-width="3"><circle cx="15" cy="15" r="12"/><path d="M9 15l4 4 8-8"/></svg>SATISFACTION GUARANTEED</div>
  </div>
</section>

<h2 class="abs section-title" style="top:1668px">FAQ</h2>

<div class="abs faq-item" style="left:132px;top:1775px">
  <div class="faq-head"><svg width="30" height="30" viewBox="0 0 30 30"><circle cx="15" cy="13" r="11" fill="var(--green)"/><rect x="11" y="24" width="8" height="5" fill="var(--green)"/></svg><h3>WHAT IS STOCK UP?</h3></div>
  <p>Sed ut perspiciatis unde omnis iste natus error sit volupta-tem accusantium doloremque laudantium aperiam, eaque ipsa &nbsp;rbeataevitaedicta sunt explicabo.</p>
</div>
<div class="abs faq-item" style="left:452px;top:1775px">
  <div class="faq-head"><svg width="30" height="30" viewBox="0 0 30 30"><circle cx="15" cy="15" r="14" fill="var(--green)"/><path d="M8 15l5 5 9-10" fill="none" stroke="#fff" stroke-width="3.5"/></svg><h3>WHAT IS YOUR SATISFACTION GUARANTEE?</h3></div>
  <p>Sed ut perspiciatis unde omnis iste natus error sit volupta-tem accusantium doloremque laudantium aperiam, eaque ipsa &nbsp;rbeataevitaedicta sunt explicabo.</p>
</div>
<div class="abs faq-item" style="left:778px;top:1775px">
  <div class="faq-head"><svg width="32" height="28" viewBox="0 0 34 28" fill="none" stroke="var(--green)" stroke-width="3"><path d="M1 2h6l4 16h18l4-12H9"/><circle cx="13" cy="24" r="2.5"/><circle cx="27" cy="24" r="2.5"/></svg><h3>SHIPPING POLICY</h3></div>
  <p>Sed ut perspiciatis unde omnis iste natus error sit volupta-tem accusantium doloremque laudantium aperiam, eaque ipsa &nbsp;rbeataevitaedicta sunt explicabo.</p>
</div>

<div class="abs faq-item" style="left:132px;top:1928px">
  <div class="faq-head"><svg width="30" height="30" viewBox="0 0 30 30"><circle cx="15" cy="15" r="12" fill="none" stroke="var(--green)" stroke-width="4"/><circle cx="15" cy="15" r="5" fill="var(--green)"/></svg><h3>WHAT DO I GET WITH MY STOCK UP PLAN?</h3></div>
  <p>Sed ut perspiciatis unde omnis iste natus error sit volupta-tem accusantium doloremque laudantium aperiam, eaque ipsa &nbsp;rbeataevitaedicta sunt explicabo.</p>
</div>
<div class="abs faq-item" style="left:452px;top:1928px">
  <div class="faq-head"><svg width="30" height="30" viewBox="0 0 30 30" fill="none" stroke="var(--green)" stroke-width="4"><path d="M5 12a10 10 0 0 1 19-3M25 18a10 10 0 0 1-19 3"/><path d="M24 2v8h-8M6 28v-8h8"/></svg><h3>RETURNS POLICY</h3></div>
  <p>Sed ut perspiciatis unde omnis iste natus error sit volupta-tem accusantium doloremque laudantium aperiam, eaque ipsa &nbsp;rbeataevitaedicta sunt explicabo.</p>
</div>
<div class="abs faq-item" style="left:778px;top:1928px">
  <div class="faq-head"><svg width="30" height="30" viewBox="0 0 30 30"><rect x="4" y="4" width="22" height="22" fill="var(--green)"/><rect x="11" y="10" width="8" height="16" fill="#fff"/></svg><h3>WHAT BRANDS DO YOU STOCK?</h3></div>
  <p>Sed ut perspiciatis unde omnis iste natus error sit volupta-tem accusantium doloremque laudantium aperiam, eaque ipsa &nbsp;rbeataevitaedicta sunt explicabo.</p>
</div>

<div class="abs faq-item" style="left:132px;top:2081px">
  <div class="faq-head"><svg width="30" height="30" viewBox="0 0 24 24" stroke="var(--green)" stroke-width="4"><path d="M3 3l18 18M21 3 3 21"/></svg><h3>WHAT IS YOUR CANCELLATION POLICY?</h3></div>
  <p>Sed ut perspiciatis unde omnis iste natus error sit volupta-tem accusantium doloremque laudantium aperiam, eaque ipsa &nbsp;rbeataevitaedicta sunt explicabo.</p>
</div>
<div class="abs faq-item" style="left:452px;top:2081px">
  <div class="faq-head"><svg width="30" height="30" viewBox="0 0 30 30"><rect x="3" y="8" width="24" height="20" rx="2" fill="var(--green)"/><circle cx="15" cy="18" r="4" fill="#fff"/></svg><h3>WHAT ABOUT SIZING?</h3></div>
  <p>Sed ut perspiciatis unde omnis iste natus error sit volupta-tem accusantium doloremque laudantium aperiam, eaque ipsa &nbsp;rbeataevitaedicta sunt explicabo.</p>
</div>
<div class="abs faq-item" style="left:778px;top:2081px">
  <div class="faq-head"><svg width="32" height="30" viewBox="0 0 32 30"><ellipse cx="16" cy="16" rx="13" ry="10" fill="var(--green)"/><rect x="8" y="22" width="4" height="6" fill="var(--green)"/><rect x="20" y="22" width="4" height="6" fill="var(--green)"/><circle cx="16" cy="5" r="3" fill="var(--green)"/></svg><h3>HOW DOES PAYMENT WORK?</h3></div>
  <p>Sed ut perspiciatis unde omnis iste natus error sit volupta-tem accusantium doloremque laudantium aperiam, eaque ipsa &nbsp;rbeataevitaedicta sunt explicabo.</p>
</div>

<footer class="abs site-footer">
  <div class="abs foot-links">How It Works &nbsp;/ &nbsp;Plans &nbsp;/ &nbsp;Faq &nbsp;/ &nbsp;About Us</div>
  <div class="abs copyright">© Copy Rights 2014 Stock Up.All Rights Reserved</div>
  <span class="abs social" style="left:850px"></span>
  <span class="abs social" style="left:896px"></span>
  <span class="abs social" style="left:942px"></span>
  <span class="abs social" style="left:988px"></span>
  <span class="abs social" style="left:1034px"></span>
  <span class="abs pay" style="left:915px;background:#c9ced6"></span>
  <span class="abs pay" style="left:955px;background:#e9ecf1"></span>
  <span class="abs pay" style="left:995px;background:#f0f0f0"></span>
  <span class="abs pay" style="left:1035px;background:#9fc0e6"></span>
</footer>

</body>
</html>
```